Telecommunications Company needs a business card design

We are looking for a sleek, professional and modern business card design based off our new logo. Will look at both light and dark options. On some designs please provide a small space for a QR code

Target Market(s)

B2B clients in Australia

Contact Information for Business Card

Name, Position, Riverside (head) office, Phone number, email address, QR code (link to our website qlinetelecom.com.au

Colors
0054AA
0677BA
7BADD7
CADEEF
E8F1F8
0094D4
00A9DD
6FCCEA
C7EBF8
E9F6FB
00AB8E
00BBA5
67D7C9
C6EFE9
E9F9F6

```html
<!DOCTYPE html>
<html lang="en">
<head>
<meta charset="utf-8">
<title>Qline Telecom – Business Card</title>
<link rel="stylesheet" href="https://fonts.googleapis.com/css2?family=Montserrat:wght@400;500;700&display=swap">
<style>
  :root {
    --backdrop: #161616;
    --card: #262626;
    --card-edge: #2e2e2e;
    --blue: #0677BA;
    --blue-bright: #0094D4;
    --text: #e9ecef;
  }
  * { box-sizing: border-box; margin: 0; padding: 0; }
  html, body {
    width: 1200px; height: 900px; overflow: hidden;
    background: var(--backdrop);
    font-family: "Montserrat", sans-serif;
  }
  .canvas {
    width: 1200px; height: 900px;
    display: flex; flex-direction: column; align-items: center; justify-content: center;
    gap: 36px;
  }
  .card {
    position: relative;
    width: 700px; height: 400px;
    background: linear-gradient(160deg, var(--card-edge), var(--card) 60%);
    border-bottom: 7px solid var(--blue);
    box-shadow: 0 18px 40px rgba(0,0,0,.55);
  }
  .card--front { display: flex; align-items: center; justify-content: center; }
  .brand { display: flex; align-items: center; gap: 18px; }
  .brand__mark { width: 34px; height: 34px; background: var(--blue-bright); }
  .brand__name {
    font-weight: 700; font-size: 52px; letter-spacing: 1px; color: var(--blue-bright);
    white-space: nowrap;
  }
  .card--back .brand { position: absolute; top: 70px; right: 60px; }
  .card--back .brand__name { font-size: 40px; }
  .card--back .brand__mark { width: 26px; height: 26px; }
  .contact {
    position: absolute; left: 52px; bottom: 48px;
    color: var(--text); font-size: 19px; line-height: 1.75;
  }
  .contact__name {
    font-weight: 700; color: var(--blue); text-transform: uppercase; font-size: 21px;
  }
  .contact__role { font-weight: 500; color: var(--text); margin-left: 6px; }
  .contact__row { display: flex; gap: 24px; white-space: nowrap; }
  .contact__item { display: inline-flex; align-items: center; gap: 8px; }
  .icon { width: 15px; height: 15px; fill: none; stroke: var(--blue-bright); stroke-width: 2; }
  .icon--solid { fill: var(--blue-bright); stroke: none; }
</style>
</head>
<body>
<main class="canvas">
  <section class="card card--front">
    <div class="brand">
      <span class="brand__mark"></span>
      <span class="brand__name">Qline Telecom</span>
    </div>
  </section>

  <section class="card card--back">
    <div class="brand">
      <span class="brand__mark"></span>
      <span class="brand__name">Qline Telecom</span>
    </div>
    <div class="contact">
      <p><span class="contact__name">Mark Ellison</span><span class="contact__role">Director</span></p>
      <div class="contact__row">
        <span class="contact__item">
          <svg class="icon" viewBox="0 0 16 16"><path d="M4 1.5l2.5 3-1.5 1.5c1 2 2.5 3.5 4.5 4.5L11 9l3 2.5-1.5 2.5C7 13.5 2.5 9 2 3.5z"/></svg>
          (07) 3555 0142
        </span>
        <span class="contact__item">
          <svg class="icon" viewBox="0 0 16 16"><rect x="1.5" y="3.5" width="13" height="9"/><path d="M1.5 3.5L8 9l6.5-5.5"/></svg>
          info@qlinetelecom.com.au
        </span>
      </div>
      <div class="contact__row">
        <span class="contact__item">
          <svg class="icon" viewBox="0 0 16 16"><circle cx="8" cy="8" r="6.5"/><path d="M1.5 8h13M8 1.5c3 3.5 3 9.5 0 13M8 1.5c-3 3.5-3 9.5 0 13"/></svg>
          www.qlinetelecom.com.au
        </span>
        <span class="contact__item">
          <svg class="icon icon--solid" viewBox="0 0 16 16"><path d="M8 1a5 5 0 0 0-5 5c0 4 5 9 5 9s5-5 5-9a5 5 0 0 0-5-5zm0 7a2 2 0 1 1 0-4 2 2 0 0 1 0 4z"/></svg>
          Riverside (head) office
        </span>
      </div>
    </div>
  </section>
</main>
</body>
</html>
```